flyer/brochure design to deliver to homes (letter box delivery)

Hi I would like something designed to represent my business Hair & Make up, I have a home based salon but offer mobile services for weddings. I really like beachy colours elegant and not to busy. but open to all different designs.

I will be getting these printed up through Korlen press the product specs are:

Document Trim Size
Horizontal
216 x 139 mm
2556 x 1642 pixels
Vertical
139 x 216 mm
1642 x 2556 pixels

Full Bleed Size
Horizontal
219 x 142 mm
2592 x 1677 pixels
Vertical
142 x 219 mm
1677 x 2592 pixels
Finished artwork should use the full bleed dimensions for best results.

I will also upload a recent business card that i have but dont have to stick to similar design

Industry/Entity Type

Salon

Requirements
Must have
• my logo (you can change the colour of my logo if you like)

would like it to have somewhere:
"look good feel great without paying silly prices"

must also have:

private home salon based in Marlow Bay, mobile service provided for weddings only

Im thinking I would like the price list on the back but open to what ever you submit

price list:
Ladies Cut $20
Ladies Blowdry $20 from
Mens cut $15
Full head of Foils, Toner, Cut & Blowdry $110
Half Head of Foils, Toner, Cut & Blowdry $80
Tint cut & colour $60-80
Tint with scattered foils Cut & Blowdry $70-$110

Wedding Package Hair & Make up $135pp mobile servive provided
check out our webpage for our complete pricelist

prices subject to change without notice

business details:

p: 0482 736 194
E: cts@quorix.com.au
W: www.coraltressstudio.com.au

I would like it to have maybe on the front as an initial eye catcher:

Full head of foils, Toner, Cut & Blowdry $110 every day

```html
<!DOCTYPE html>
<html lang="en">
<head>
<meta charset="utf-8">
<title>Coral Tress Studio – Flyer</title>
<link rel="stylesheet" href="https://fonts.googleapis.com/css2?family=Arimo:wght@400;700&display=swap">
<style>
  :root {
    --card-black: #050505;
    --page-bg: #d9d9d9;
    --white: #ffffff;
    --teal: #3fd3c2;
    --aqua: #42c6d8;
    --blue: #2f6fd6;
    --pink: #d21f9c;
    --grey: #bdbdbd;
    --rule: #3a3a3a;
  }
  * { margin: 0; padding: 0; box-sizing: border-box; }
  html, body {
    width: 1200px;
    height: 778px;
    overflow: hidden;
    background: var(--page-bg);
  }
  .flyer {
    position: relative;
    width: 1200px;
    height: 778px;
    overflow: hidden;
    background: var(--card-black);
    font-family: "Arimo", Helvetica, Arial, sans-serif;
    color: var(--white);
  }
  .service-list {
    position: absolute;
    top: 30px;
    right: 60px;
    font-size: 13px;
    letter-spacing: 0.08em;
    color: var(--teal);
    text-transform: uppercase;
    white-space: nowrap;
  }
  .service-list .dot { color: var(--pink); margin: 0 8px; }

  /* left column: illustration, name, salon detail */
  .hair-illustration {
    position: absolute;
    left: 105px;
    top: 70px;
    width: 240px;
    height: 390px;
    border-radius: 48% 52% 30% 30% / 40% 40% 26% 26%;
    background: linear-gradient(160deg, var(--blue) 0%, var(--aqua) 45%, var(--teal) 100%);
  }
  .brand-name {
    position: absolute;
    left: 50px;
    top: 485px;
    width: 350px;
    text-align: center;
    font-size: 34px;
    font-weight: 700;
    line-height: 1.1;
    color: var(--pink);
    text-transform: uppercase;
    white-space: nowrap;
  }
  .salon-detail {
    position: absolute;
    left: 50px;
    top: 580px;
    width: 350px;
    text-align: center;
    font-size: 15px;
    line-height: 1.45;
    color: var(--grey);
  }

  /* right column: offer, tagline, prices */
  .headline {
    position: absolute;
    top: 70px;
    right: 60px;
    text-align: right;
    font-size: 44px;
    font-weight: 400;
    line-height: 1.12;
    letter-spacing: -0.01em;
    white-space: nowrap;
  }
  .headline .every-day {
    display: block;
    margin-top: 6px;
    font-size: 22px;
    font-weight: 700;
    color: var(--teal);
    text-transform: uppercase;
    letter-spacing: 0.08em;
  }
  .tagline {
    position: absolute;
    top: 232px;
    right: 60px;
    font-size: 21px;
    color: var(--pink);
    white-space: nowrap;
  }
  .price-list {
    position: absolute;
    left: 470px;
    right: 60px;
    top: 280px;
    list-style: none;
    border-top: 1px solid var(--rule);
  }
  .price-list li {
    display: flex;
    justify-content: space-between;
    align-items: baseline;
    padding: 5px 0;
    font-size: 17px;
    border-bottom: 1px solid var(--rule);
    white-space: nowrap;
  }
  .price-list .price { color: var(--teal); font-weight: 700; }
  .price-list .package { color: var(--pink); font-weight: 700; }
  .price-list .package .price { color: var(--pink); }
  .price-notes {
    position: absolute;
    left: 470px;
    right: 60px;
    top: 568px;
    display: flex;
    justify-content: space-between;
    font-size: 13px;
    color: var(--grey);
    white-space: nowrap;
  }

  /* bottom contact row */
  .divider {
    position: absolute;
    left: 440px;
    top: 640px;
    width: 1px;
    height: 100px;
    background: var(--grey);
  }
  .contact {
    position: absolute;
    left: 470px;
    top: 645px;
  }
  .contact .call {
    font-size: 14px;
    font-weight: 700;
    color: var(--teal);
    text-transform: uppercase;
    letter-spacing: 0.02em;
    white-space: nowrap;
  }
  .contact .call span { font-size: 19px; }
  .contact .stylist {
    margin-top: 8px;
    font-size: 28px;
    text-transform: uppercase;
    white-space: nowrap;
  }
  .contact .role {
    margin-top: 6px;
    font-size: 17px;
    color: var(--grey);
  }
  .web-details {
    position: absolute;
    right: 60px;
    top: 662px;
    text-align: right;
    font-size: 17px;
    line-height: 1.6;
    white-space: nowrap;
  }
  .web-details b { color: var(--teal); margin-right: 6px; }
</style>
</head>
<body>
  <main class="flyer">
    <p class="service-list">Mobile Services<span class="dot">•</span>Hairstyling<span class="dot">•</span>Bridal<span class="dot">•</span>Special Occasions<span class="dot">•</span>Fashion</p>

    <div class="hair-illustration" role="img" aria-label="Stylised illustration of a woman with swirling blue and teal hair"></div>
    <p class="brand-name">Coral Tress<br>Studio</p>
    <p class="salon-detail">Private home salon based in Marlow Bay.<br>Mobile service provided for weddings only.</p>

    <h1 class="headline">Full head of Foils, Toner,<br>Cut &amp; Blowdry for $110<span class="every-day">Every day</span></h1>
    <p class="tagline">Look good, feel great without paying silly prices</p>

    <ul class="price-list">
      <li><span>Ladies Cut</span><span class="price">$20</span></li>
      <li><span>Ladies Blowdry</span><span class="price">from $20</span></li>
      <li><span>Mens Cut</span><span class="price">$15</span></li>
      <li><span>Half Head of Foils, Toner, Cut &amp; Blowdry</span><span class="price">$80</span></li>
      <li><span>Tint, Cut &amp; Colour</span><span class="price">$60–80</span></li>
      <li><span>Tint with scattered Foils, Cut &amp; Blowdry</span><span class="price">$70–110</span></li>
      <li class="package"><span>Wedding Package Hair &amp; Make-up, mobile service</span><span class="price">$135pp</span></li>
    </ul>
    <p class="price-notes"><span>Check out our webpage for our complete price list</span><span>Prices subject to change without notice</span></p>

    <div class="divider"></div>
    <div class="contact">
      <p class="call">Call <span>0482 736 194</span> for appointment</p>
      <p class="stylist">Maren Holloway</p>
      <p class="role">Make-up Artist</p>
    </div>
    <p class="web-details"><b>E</b>cts@quorix.com.au<br><b>W</b>www.coraltressstudio.com.au</p>
  </main>
</body>
</html>
```